7 P's for Healthcare Companies - Textbook Graphic

Can you create a graphic for me for a medical textbook? The goal is to show 7 critical features of a healthcare startup and the audience is physicians with limited business backgrounds.

Please include a picture of young, male emergency physician in the middle of the graphic. Show them evaluating an idea. Can you surround the physician with bold writing for the seven components, and use brief descriptions and simple images or graphics to illustrate the point?

The image should be somewhat formal, but it's OK to be lighthearded.

The seven P's and brief descriptions include the following:
Product: what is their market solution?
(Intellectual) Property: do they have a patent or trademark?
Product Clearance: how will they get RLT approval and NVB clearance?
Payment: how will they make money?
Pilots: have they applied their product in a healthcare setting?
Physician and Patient feedback: Do doctors and patients like their product?
Publication: do they have evidence their product works?

More detail and information is available at this website: https://kovantrel.com/blog/uncategorized/healthcare-framework/

I will need to own this image

```html
<!DOCTYPE html>
<html lang="en">
<head>
<meta charset="utf-8">
<title>7 P's for Healthcare Companies</title>
<link rel="stylesheet" href="https://fonts.googleapis.com/css2?family=Archivo+Black&family=Poppins:wght@500;700;800&display=swap">
<style>
  :root {
    --ink: #1e2b3c;
    --paper: #ffffff;
    --figure-light: #eef1f5;
    --figure-dark: #d6dce4;
  }
  html, body {
    margin: 0;
    padding: 0;
    width: 1200px;
    height: 1200px;
    overflow: hidden;
    background: var(--paper);
  }
  .framework {
    display: block;
    width: 1200px;
    height: 1200px;
  }
  .ring { fill: none; stroke: var(--ink); stroke-width: 17; }
  .node-disc { fill: var(--paper); stroke: var(--ink); stroke-width: 9; }
  .icon { fill: none; stroke: var(--ink); stroke-width: 3.6; stroke-linecap: round; stroke-linejoin: round; }
  .icon-fill { fill: var(--ink); stroke: none; }
  .label-initial { font-family: "Poppins", sans-serif; font-weight: 500; font-size: 88px; fill: var(--ink); }
  .label-word { font-family: "Archivo Black", sans-serif; font-size: 22px; fill: var(--ink); letter-spacing: 0.5px; }
  .label-note { font-family: "Archivo Black", sans-serif; font-size: 8px; fill: var(--ink); }
  .title { font-family: "Poppins", sans-serif; font-weight: 800; font-size: 168px; fill: var(--ink); letter-spacing: -6px; }
  .title-backing { fill: var(--paper); }
</style>
</head>
<body>
<svg class="framework" viewBox="0 0 1200 1200" xmlns="http://www.w3.org/2000/svg">
  <defs>
    <linearGradient id="figureTone" x1="0" y1="0" x2="0" y2="1">
      <stop offset="0" stop-color="var(--figure-light)"/>
      <stop offset="1" stop-color="var(--figure-dark)"/>
    </linearGradient>
  </defs>

  <circle class="ring" cx="614" cy="596" r="346"/>

  <!-- central physician -->
  <rect class="physician" x="453" y="340" width="335" height="392" rx="24" fill="url(#figureTone)"
        role="img" aria-label="Line drawing of a young male emergency physician in a white coat, tie and stethoscope, smiling as he evaluates an idea"/>

  <rect class="title-backing" x="446" y="690" width="340" height="150"/>
  <text class="title" x="616" y="826" text-anchor="middle">7P’s</text>

  <!-- Publication -->
  <g class="node node-publication" transform="translate(464 288)">
    <circle class="node-disc" r="91"/>
    <g class="icon">
      <path d="M-42 12 L-18 -2 L2 -30 L28 22 L-8 26 L-28 32 Q-40 34 -45 24 Z"/>
      <ellipse cx="15" cy="-4" rx="13" ry="28" transform="rotate(-25 15 -4)"/>
      <path d="M-18 30 L-6 50 Q-2 56 6 50 L-4 30"/>
      <path d="M32 -28 Q48 -12 40 8"/>
      <path d="M38 -42 Q62 -14 50 14"/>
    </g>
  </g>
  <text class="label-initial" x="416" y="170">P</text>
  <text class="label-word" x="435" y="170">UBLICATION</text>

  <!-- Product -->
  <g class="node node-product" transform="translate(766 286)">
    <circle class="node-disc" r="91"/>
    <g class="icon">
      <path d="M-47 4 L0 -14 L47 4 L0 28 Z"/>
      <path d="M-47 4 L-52 14 L-4 40 L0 28"/>
      <path d="M47 4 L52 14 L4 40 L0 28"/>
      <path d="M-42 16 L-42 42 L0 66 L42 42 L42 16"/>
      <path d="M0 28 L0 66"/>
      <path d="M-7 -8 L-7 -18 Q-20 -26 -18 -40 Q-15 -54 0 -55 Q15 -54 18 -40 Q20 -26 7 -18 L7 -8"/>
      <path d="M-6 -4 L6 -4 M-4 1 L4 1"/>
      <path d="M0 -64 L0 -74 M-24 -56 L-30 -64 M24 -56 L30 -64 M-34 -38 L-44 -42 M34 -38 L44 -42"/>
    </g>
  </g>
  <text class="label-initial" x="735" y="172">P</text>
  <text class="label-word" x="754" y="172">RODUCT</text>

  <!-- Intellectual Property -->
  <g class="node node-property" transform="translate(955 522)">
    <circle class="node-disc" r="91"/>
    <g class="icon">
      <path d="M-40 -54 L28 -54 Q38 -54 38 -40 L38 50 Q38 56 30 56 L-44 56 Q-50 56 -50 50 L-50 42 L26 42"/>
      <path d="M-40 -54 Q-46 -54 -44 -44 L-42 42"/>
      <path d="M28 -54 Q44 -54 44 -38 L38 -38"/>
      <path d="M-30 -38 L18 -38 M-30 -26 L18 -26 M-30 -14 L4 -14"/>
      <circle cx="12" cy="6" r="10"/>
      <circle cx="12" cy="6" r="4"/>
      <path d="M4 16 L0 30 L6 27 M20 16 L24 30 L18 27"/>
    </g>
  </g>
  <text class="label-note" x="997" y="382">(INTELLECTUAL)</text>
  <text class="label-initial" x="958" y="405">P</text>
  <text class="label-word" x="977" y="405">ROPERTY</text>

  <!-- Product Clearance -->
  <g class="node node-clearance" transform="translate(888 816)">
    <circle class="node-disc" r="91"/>
    <g class="icon">
      <rect x="-46" y="-50" width="92" height="114" rx="8"/>
      <rect x="-16" y="-60" width="32" height="16" rx="4" class="icon-fill"/>
      <circle cx="-26" cy="-14" r="10"/>
      <path d="M-31 -14 L-27 -10 L-20 -18"/>
      <circle cx="-26" cy="12" r="10"/>
      <path d="M-31 12 L-27 16 L-20 8"/>
      <path d="M-8 -20 L34 -20 M-8 -8 L34 -8 M-8 6 L34 6 M-8 18 L34 18 M-36 42 L34 42"/>
    </g>
  </g>
  <text class="label-initial" x="887" y="984">P</text>
  <text class="label-word" x="906" y="984">RODUCT</text>
  <text class="label-word" x="881" y="1008">CLEARANCE</text>

  <!-- Payment -->
  <g class="node node-payment" transform="translate(616 947)">
    <circle class="node-disc" r="91"/>
    <g class="icon">
      <rect x="-52" y="-58" width="104" height="62"/>
      <rect x="-44" y="-50" width="88" height="46" rx="6"/>
      <circle cx="0" cy="-27" r="17"/>
      <path d="M6 -34 Q0 -38 -5 -34 Q-8 -28 0 -27 Q8 -25 5 -19 Q0 -16 -6 -20 M0 -42 L0 -38 M0 -16 L0 -12"/>
      <path d="M-60 30 Q-46 22 -38 24 Q-20 26 -4 28 Q6 30 4 36 Q0 40 -20 38"/>
      <path d="M-4 36 Q20 32 40 22 Q50 18 52 26 Q50 32 30 42 Q10 52 -20 48 L-48 52"/>
    </g>
  </g>
  <text class="label-initial" x="573" y="1109">P</text>
  <text class="label-word" x="592" y="1109">AYMENT</text>

  <!-- Pilots -->
  <g class="node node-pilots" transform="translate(344 816)">
    <circle class="node-disc" r="91"/>
    <g class="icon">
      <path d="M-16 -50 L-14 -24 Q-10 4 12 6 Q32 4 36 -24 L38 -50"/>
      <path d="M-12 -20 Q12 0 34 -20"/>
       <circle cx="-16" cy="-52" r="4" class="icon-fill"/>
      <circle cx="-2" cy="-54" r="5" class="icon-fill"/>
      <circle cx="24" cy="-54" r="5" class="icon-fill"/>
      <path d="M12 6 Q20 30 14 44 Q6 60 -14 58 Q-36 56 -42 42 Q-46 30 -32 16 Q-26 8 -28 0"/>
      <circle cx="-36" cy="-14" r="12"/>
      <circle cx="-36" cy="-14" r="5" class="icon-fill"/>
      <path d="M-24 -14 Q-18 -6 -24 2"/>
    </g>
  </g>
  <text class="label-initial" x="238" y="956">P</text>
  <text class="label-word" x="257" y="956">ILOTS</text>

  <!-- Physician and Patient Feedback -->
  <g class="node node-feedback" transform="translate(278 522)">
    <circle class="node-disc" r="91"/>
    <g class="icon">
      <path d="M-56 -44 Q-56 -50 -50 -50 L16 -50 Q22 -50 22 -44 L22 -4 Q22 2 16 2 L-20 2 L-40 20 L-40 2 L-50 2 Q-56 2 -56 -4 Z"/>
      <path d="M30 -20 L52 -20 Q58 -20 58 -14 L58 22 Q58 28 52 28 L48 28 L48 44 L34 28 L0 28 Q-8 28 -8 20 L-8 12"/>
      <path class="icon-fill" d="M-17 -12 L-33 -28 Q-38 -36 -30 -40 Q-22 -42 -17 -34 Q-12 -42 -4 -40 Q4 -36 -1 -28 Z"/>
    </g>
  </g>
  <text class="label-initial" x="105" y="372">P</text>
  <text class="label-word" x="124" y="372">HYSICIAN</text>
  <text class="label-word" x="99" y="400">AND PATIENT</text>
  <text class="label-word" x="116" y="428">FEEDBACK</text>
</svg>
</body>
</html>
```